Design Startseite Kanzlei-Homepage
Zielgruppe
Wir sind eine Rechtsanwaltskanzlei in Kempten (Allgäu) und regional sowie überregional in verschiedenen Rechtsgebieten tätig. Unsere Zielgruppe sind sowohl private als auch gewerbliche Mandanten.
Aufgabenstellung
Die bestehende Gestaltung wirkt derzeit aus unserer Sicht überholt. Insbesondere soll das bislang dominierende Rot vollständig entfallen.
Stattdessen stellen wir uns ein modernes, hochwertiges Erscheinungsbild vor, primär in dunklen Farbtönen (Anthrazit/Schwarz) kombiniert mit Beige- bzw. warmen Naturtönen. Ziel ist eine klare visuelle Anlehnung an unsere Kanzleiräumlichkeiten (siehe Fotos).
Die Webseite soll insgesamt moderner, klarer und visuell anspruchsvoller wirken, ohne an Seriosität und Zugänglichkeit einzubüßen. Die Balance zwischen hochwertigem Erscheinungsbild und mandantenorientierter Nutzerführung steht für uns im Vordergrund.

```html
<!DOCTYPE html>
<html lang="de">
<head>
<meta charset="utf-8">
<title>Kanzlei am Lindenhof – Rechtsanwälte in Kempten</title>
<link href="https://fonts.googleapis.com/css2?family=DM+Sans:wght@400;500;700&family=Playfair+Display:wght@400;500&display=swap" rel="stylesheet">
<style>
:root{
  --ink:#1c1c1e;
  --ink-2:#2a2a2d;
  --ink-3:#333336;
  --sand:#efe9df;
  --paper:#f7f4ee;
  --gold:#c8b791;
  --gold-2:#b39f78;
  --text:#2b2b2b;
  --muted:#77726a;
  --muted-dark:#8a8680;
  --line:#e2dbcf;
  --white:#ffffff;
}
*{box-sizing:border-box;margin:0;padding:0}
html,body{width:1200px;height:3276px;overflow:hidden}
body{font-family:"DM Sans",Arial,sans-serif;color:var(--text);background:var(--ink);position:relative}
.serif{font-family:"Playfair Display",Georgia,serif;font-weight:400}
section,header{position:absolute;left:0;width:1200px}
.abs{position:absolute}
.eyebrow{font-size:7px;letter-spacing:2px;text-transform:uppercase;color:var(--gold-2);display:flex;align-items:center;gap:10px}
.eyebrow::before{content:"";width:18px;height:1px;background:var(--gold-2)}

/* top bar + nav */
.topbar{top:0;height:22px;background:var(--ink-2);color:#9d9992;font-size:8px}
.topbar .info{right:140px;top:6px}
.topbar .phone{right:36px;top:6px;display:flex;gap:6px;align-items:center;color:#c9c5bd}
.nav{top:22px;height:65px;background:var(--ink)}
.brand{left:70px;top:19px;color:var(--white);font-weight:700;font-size:21px;letter-spacing:.5px;display:flex;align-items:center;gap:8px}
.brand .mark{width:9px;height:9px;background:var(--gold)}
.menu{left:445px;top:29px;display:flex;gap:26px;font-size:10px;letter-spacing:1px;color:#d9d5cd}
.menu .active{color:var(--white);font-weight:700}
.nav-cta{right:36px;top:21px;width:126px;height:22px;border:1px solid var(--gold-2);color:var(--gold);font-size:7.5px;letter-spacing:1px;display:flex;align-items:center;justify-content:center}

/* hero */
.hero{top:87px;height:534px;background:var(--ink)}
.hero-photo{left:0;top:0;width:1200px;height:534px;background:linear-gradient(90deg,#1f1f20 0%,#2b2b2c 32%,#5e5a55 55%,#8b8782 75%,#5a6266 100%)}
.hero-shade{left:0;top:0;width:1200px;height:534px;background:linear-gradient(90deg,rgba(20,20,21,.92) 0%,rgba(20,20,21,.55) 45%,rgba(20,20,21,.1) 100%)}
.hero .eyebrow{left:72px;top:143px;color:#c7c1b6}
.hero .eyebrow::before{width:34px;background:#c7c1b6;margin-right:6px}
.hero h1{left:72px;top:165px;font-size:38px;line-height:41px;color:var(--white)}
.hero h1 span{color:var(--gold)}
.hero p{left:72px;top:310px;width:500px;font-size:9.5px;line-height:17px;color:#d3cfc7}
.btn-gold{left:72px;top:405px;width:341px;height:31px;background:var(--gold);color:var(--ink);font-size:8px;font-weight:700;letter-spacing:1.5px;display:flex;align-items:center;justify-content:center;gap:72px}
.btn-line{left:433px;top:405px;width:161px;height:31px;border:1px solid #55524d;color:#d3cfc7;font-size:8px;letter-spacing:1.5px;display:flex;align-items:center;justify-content:center}
.quote{left:849px;top:463px;width:290px;height:71px;background:rgba(42,42,45,.85);padding:16px 34px;color:#d3cfc7;font-size:10px;line-height:15px}
.quote::after{content:"";position:absolute;left:34px;bottom:8px;width:28px;height:1px;background:var(--gold-2)}

/* stats */
.stats{top:621px;height:67px;background:var(--ink-2)}
.stat{top:18px}
.stat b{display:block;font-family:"Playfair Display",Georgia,serif;font-weight:400;color:var(--gold);font-size:18px}
.stat small{font-size:7px;color:#8d8982}
.stat-div{top:0;width:1px;height:67px;background:#3a3a3d}

/* competence cards */
.areas{top:688px;height:597px;background:var(--sand)}
.areas h2{left:0;width:1200px;top:56px;text-align:center;font-size:23px;line-height:26px;color:var(--ink)}
.card{width:247px;background:var(--ink-2)}
.card .ph{height:160px}
.card .bar{height:41px;display:flex;align-items:center;gap:12px;padding-left:14px;color:var(--white);font-size:9px;font-weight:700;letter-spacing:.6px}
.card .bar.tall{height:45px;line-height:12px}
.card svg{flex:none}

/* legal fields */
.fields{top:1285px;height:637px;background:var(--paper)}
.fields .eyebrow{left:255px;top:84px}
.fields h2{left:255px;top:113px;font-size:30px;color:var(--ink)}
.fields .lead{left:620px;top:89px;width:310px;font-size:9px;line-height:17px;color:var(--muted)}
.cell{width:230px;padding:28px 22px 0 23px}
.cell .ic{width:26px;height:26px;border:1px solid var(--line);display:flex;align-items:center;justify-content:center;margin-bottom:13px}
.cell h3{font-family:"Playfair Display",Georgia,serif;font-weight:400;font-size:14px;color:var(--ink);margin-bottom:8px}
.cell p{font-size:8px;line-height:15px;color:var(--muted);margin-bottom:10px}
.cell a{font-size:6.5px;letter-spacing:1.5px;color:var(--gold-2);text-decoration:none}
.vline{width:1px;background:var(--line)}
.hline{height:1px;background:var(--line)}

/* why */
.why{top:1922px;height:305px;background:var(--ink)}
.why .eyebrow{left:255px;top:114px;color:#c7c1b6}
.why h2{left:255px;top:138px;font-size:28px;line-height:32px;color:var(--white)}
.why h2 span{color:var(--gold)}
.why-item{width:205px}
.why-item h4{font-size:9px;font-weight:500;color:var(--white);margin-bottom:9px}
.why-item p{font-size:8px;line-height:14px;color:#7c7872}
.why-div{left:745px;width:1px;background:#333336}

/* team */
.team{top:2227px;height:518px;background:var(--sand)}
.team .eyebrow{left:255px;top:84px}
.team h2{left:255px;top:104px;font-size:30px;color:var(--ink)}
.team .all{left:869px;top:120px;font-size:7.5px;letter-spacing:1.5px;color:var(--ink);font-weight:500;border-bottom:1px solid var(--gold-2);padding-bottom:3px}
.member{top:173px;width:162px;background:var(--paper)}
.member .ph{height:215px;background:linear-gradient(180deg,#eceff1 0%,#dfe3e6 60%,#3a3e44 100%)}
.member .info{height:53px;padding:14px 12px 0}
.member h4{font-family:"Playfair Display",Georgia,serif;font-weight:400;font-size:10.5px;color:var(--ink)}
.member small{font-size:6.5px;letter-spacing:.8px;color:var(--gold)}

/* contact + footer */
.cta{top:2745px;height:531px;background:var(--ink)}
.cta h2{left:244px;top:76px;font-size:23px;line-height:28px;color:var(--white)}
.cta h2 span{color:var(--gold)}
.cta .tel{left:809px;top:60px;display:flex;align-items:center;gap:14px;color:var(--gold);font-family:"Playfair Display",Georgia,serif;font-size:18px}
.cta .hours{left:829px;top:88px;font-size:7.5px;color:#6f6b65}
.cta .form{left:808px;top:107px;width:146px;height:28px;background:var(--gold);color:var(--ink);font-size:7.5px;letter-spacing:1.3px;font-weight:700;display:flex;align-items:center;justify-content:center;gap:8px}
.foot-brand{left:237px;top:234px;color:var(--white);font-family:"Playfair Display",Georgia,serif;font-size:15px}
.foot-sub{left:237px;top:258px;font-size:6.5px;letter-spacing:1px;color:#6f6b65}
.foot-addr{left:237px;top:282px;font-size:8px;line-height:15px;color:#c5c1b9}
.foot-mail{left:237px;top:322px;font-size:8px;line-height:15px;color:#c5c1b9}
.foot-col h5{font-size:6.5px;letter-spacing:1.5px;color:var(--gold-2);font-weight:500;margin-bottom:14px}
.foot-col li{list-style:none;font-size:8px;color:#807c76;margin-bottom:10px}
.legal{left:38px;top:443px;display:flex;gap:20px;font-size:7.5px;color:#6a665f}
.copy{right:36px;top:443px;font-size:7.5px;color:#5c5953}
.foot-rule{left:38px;top:428px;width:1124px;height:1px;background:#2c2c2f}
</style>
</head>
<body>

<header class="topbar">
  <span class="abs info">Infos &amp; Terminvereinbarung</span>
  <span class="abs phone">
    <svg width="8" height="8" viewBox="0 0 24 24" fill="#c9c5bd"><path d="M6.6 10.8a15.1 15.1 0 006.6 6.6l2.2-2.2a1 1 0 011-.25 11.4 11.4 0 003.6.57 1 1 0 011 1V20a1 1 0 01-1 1A17 17 0 013 4a1 1 0 011-1h3.5a1 1 0 011 1c0 1.25.2 2.45.57 3.57a1 1 0 01-.25 1z"/></svg>
    0831 · 472 906 20
  </span>
</header>

<header class="nav">
  <div class="abs brand"><span>KANZLEI AM LINDENHOF</span><span class="mark"></span></div>
  <nav class="abs menu">
    <span class="active">STARTSEITE</span><span>RECHTSGEBIETE</span><span>KANZLEI</span><span>STANDORT</span><span>KONTAKT</span>
  </nav>
  <div class="abs nav-cta">TERMIN VEREINBAREN</div>
</header>

<section class="hero">
  <div class="abs hero-photo" role="img" aria-label="Foto: zwei Anwälte im Gespräch am Besprechungstisch, Zimmerpflanze im Hintergrund"></div>
  <div class="abs hero-shade"></div>
  <div class="abs eyebrow">Rechtsanwälte &amp; Fachanwälte · Kempten im Allgäu</div>
  <h1 class="abs serif">Recht.<br><span>Klar. Kompetent.<br>Persönlich.</span></h1>
  <p class="abs">Die Kanzlei am Lindenhof berät und vertritt Mandanten in Kempten und dem gesamten Allgäu in allen wesentlichen Rechtsbereichen – mit einem spezialisierten Anwaltsteam, kurzen Wegen und echter Erreichbarkeit.</p>
  <div class="abs btn-gold"><span>UNSERE RECHTSGEBIETE</span><svg width="5" height="6" viewBox="0 0 5 6"><path d="M0 0l5 3-5 3z" fill="#1c1c1e"/></svg></div>
  <div class="abs btn-line">JETZT ANRUFEN</div>
  <div class="abs quote serif">„Ihre rechtlichen Interessen – klar vertreten, persönlich begleitet.“</div>
</section>

<section class="stats">
  <div class="abs stat" style="left:42px"><b>7+</b><small>Fachanwälte</small></div>
  <div class="abs stat-div" style="left:400px"></div>
  <div class="abs stat" style="left:440px"><b>8</b><small>Rechtsgebiete</small></div>
  <div class="abs stat-div" style="left:800px"></div>
  <div class="abs stat" style="left:838px"><b>24h</b><small>Erreichbarkeit</small></div>
</section>

<section class="areas">
  <h2 class="abs serif">Kompetenz in vielen Bereichen des<br>Rechts</h2>
  <div class="abs card" style="left:204px;top:124px">
    <div class="ph" role="img" aria-label="Foto: Hände halten eine Papierfiguren-Kette" style="background:linear-gradient(135deg,#9c9c9c,#d6d4d0)"></div>
    <div class="bar"><svg width="13" height="13" viewBox="0 0 24 24" fill="none" stroke="#fff" stroke-width="1.6"><circle cx="12" cy="8" r="4"/><path d="M4 21c1-5 15-5 16 0"/></svg>FAMILIENRECHT</div>
  </div>
  <div class="abs card" style="left:477px;top:124px">
    <div class="ph" role="img" aria-label="Foto: zwei Geschäftsleute im Gespräch am Tisch" style="background:linear-gradient(135deg,#4d5a63,#b6bcbf)"></div>
    <div class="bar"><svg width="13" height="13" viewBox="0 0 24 24" fill="none" stroke="#fff" stroke-width="1.6"><rect x="3" y="7" width="18" height="13" rx="1"/><path d="M9 7V4h6v3M3 12h18"/></svg>ARBEITSRECHT</div>
  </div>
  <div class="abs card" style="left:750px;top:124px">
    <div class="ph" role="img" aria-label="Foto: Stadtstraße mit Verkehr in der Abenddämmerung" style="background:linear-gradient(180deg,#8c8f98,#4a4f5a 55%,#2a2d33)"></div>
    <div class="bar"><svg width="14" height="13" viewBox="0 0 24 24" fill="none" stroke="#fff" stroke-width="1.6"><circle cx="8" cy="8" r="5"/><path d="M14 21l3-6 3 6M15.2 19h3.6"/></svg>VERKEHRSRECHT</div>
  </div>
  <div class="abs card" style="left:204px;top:340px">
    <div class="ph" role="img" aria-label="Foto: Justitia-Statue unter Glasdach, schwarz-weiß" style="background:linear-gradient(135deg,#bdbdbd,#555)"></div>
    <div class="bar"><svg width="14" height="13" viewBox="0 0 24 24" fill="none" stroke="#fff" stroke-width="1.6"><path d="M12 3v18M7 21h10M4 7h16M6 7l-3 7h6zM18 7l-3 7h6z"/></svg>STRAFRECHT</div>
  </div>
  <div class="abs card" style="left:477px;top:340px">
    <div class="ph" role="img" aria-label="Foto: Testamentsdokument auf dem Tisch" style="background:linear-gradient(135deg,#f2f2f2,#c9c9c9)"></div>
    <div class="bar"><svg width="12" height="13" viewBox="0 0 24 24" fill="#fff"><path d="M5 2h10l5 5v15H5z"/><path d="M8 12h8M8 16h8" stroke="#2a2a2d" stroke-width="1.6"/></svg>ERBRECHT</div>
  </div>
  <div class="abs card" style="left:750px;top:340px">
    <div class="ph" role="img" aria-label="Foto: Hausmodell mit Schlüssel auf Holztisch" style="background:linear-gradient(135deg,#9a7a5a,#d2b89a)"></div>
    <div class="bar tall"><svg width="14" height="14" viewBox="0 0 24 24" fill="none" stroke="#fff" stroke-width="1.6"><path d="M3 11l9-7 9 7v10H3z"/><path d="M10 21v-6h4v6"/></svg><span>MIET- &amp;<br>WOHNUNGSEIGENTUMSRECHT</span></div>
  </div>
</section>

<section class="fields">
  <div class="abs eyebrow">Was wir für Sie tun</div>
  <h2 class="abs serif">Unsere Rechtsgebiete</h2>
  <p class="abs lead">Unser Team aus spezialisierten Rechtsanwältinnen und Rechtsanwälten deckt die wichtigsten Rechtsbereiche des Alltags- und Wirtschaftslebens ab – so können Sie alle Ihre Anliegen aus einer Hand betreuen lassen.</p>

  <div class="abs vline" style="left:485px;top:181px;height:379px"></div>
  <div class="abs vline" style="left:715px;top:181px;height:379px"></div>
  <div class="abs hline" style="left:255px;top:378px;width:691px"></div>

  <div class="abs cell" style="left:255px;top:181px">
    <div class="ic"><svg width="11" height="11" viewBox="0 0 24 24" fill="none" stroke="#8a8680" stroke-width="1.6"><path d="M12 20s-8-5-8-11a4 4 0 018-1 4 4 0 018 1c0 6-8 11-8 11z"/></svg></div>
    <h3>Familienrecht</h3>
    <p>Scheidung, Sorge- und Umgangsrecht, Unterhalt, Ehevertrag – wir begleiten Sie einfühlsam und zielorientiert durch private Rechtsangelegenheiten.</p>
    <a>MEHR ERFAHREN ›</a>
  </div>
  <div class="abs cell" style="left:485px;top:181px">
    <div class="ic"><svg width="11" height="11" viewBox="0 0 24 24" fill="none" stroke="#8a8680" stroke-width="1.6"><rect x="3" y="7" width="18" height="13"/><path d="M9 7V4h6v3"/></svg></div>
    <h3>Arbeitsrecht</h3>
    <p>Kündigung, Aufhebungsvertrag, Abfindung, Arbeitszeugnis – für Arbeitnehmer und Arbeitgeber, außergerichtlich und vor Gericht.</p>
    <a>MEHR ERFAHREN ›</a>
  </div>
  <div class="abs cell" style="left:715px;top:181px">
    <div class="ic"><svg width="11" height="11" viewBox="0 0 24 24" fill="none" stroke="#8a8680" stroke-width="1.6"><path d="M5 14l2-6h10l2 6v5H5zM5 14h14"/></svg></div>
    <h3>Verkehrsrecht</h3>
    <p>Unfallereignisse, Bußgeldverfahren, Fahrerlaubnisentzug, Schadensersatz – wir setzen Ihre Ansprüche schnell und wirksam durch.</p>
    <a>MEHR ERFAHREN ›</a>
  </div>
  <div class="abs cell" style="left:255px;top:380px">
    <div class="ic"><svg width="11" height="11" viewBox="0 0 24 24" fill="none" stroke="#8a8680" stroke-width="1.6"><path d="M12 3l8 3v6c0 5-4 8-8 9-4-1-8-4-8-9V6z"/></svg></div>
    <h3>Strafrecht</h3>
    <p>Kompetente Strafverteidigung und Beratung bei Ermittlungsverfahren, Durchsuchungen und Verhandlungen – kurzfristig und vertraulich.</p>
    <a>MEHR ERFAHREN ›</a>
  </div>
  <div class="abs cell" style="left:485px;top:380px">
    <div class="ic"><svg width="11" height="11" viewBox="0 0 24 24" fill="none" stroke="#8a8680" stroke-width="1.6"><path d="M6 2h9l4 4v16H6zM9 13h7M9 17h7"/></svg></div>
    <h3>Erbrecht</h3>
    <p>Testament, Erbauseinandersetzung, Pflichtteil – fundierte Beratung bei Erbfällen, vor und nach dem Todesfall.</p>
    <a>MEHR ERFAHREN ›</a>
  </div>
  <div class="abs cell" style="left:715px;top:380px">
    <div class="ic"><svg width="11" height="11" viewBox="0 0 24 24" fill="none" stroke="#8a8680" stroke-width="1.6"><path d="M3 11l9-7 9 7v10H3z"/><path d="M10 21v-6h4v6"/></svg></div>
    <h3>Mietrecht</h3>
    <p>Mietverträge, Kündigungen, Mieterhöhungen, WEG-Recht – für Vermieter und Mieter im Allgäu.</p>
    <a>MEHR ERFAHREN ›</a>
  </div>
</section>

<section class="why">
  <div class="abs eyebrow">Warum Kanzlei am Lindenhof</div>
  <h2 class="abs serif">Kompetenz,<br><span>die Sie spüren.</span></h2>
  <div class="abs why-div" style="top:62px;height:200px"></div>
  <div class="abs why-item" style="left:532px;top:68px"><h4>Spezialisiertes Team</h4><p>Sieben Rechtsanwältinnen und Rechtsanwälte mit ausgewiesenen Fachgebieten – Ihr Anliegen landet stets in den richtigen Händen.</p></div>
  <div class="abs why-item" style="left:757px;top:68px"><h4>Kurzfristige Termine</h4><p>Wir wissen: Rechtsfragen dulden keinen Aufschub. Deshalb garantieren wir rasche Terminvergabe – auch in dringenden Situationen.</p></div>
  <div class="abs why-item" style="left:532px;top:170px"><h4>Persönliche Betreuung</h4><p>Kein Callcenter, kein Pingpong zwischen Mitarbeitern. Sie sprechen direkt mit Ihrem Anwalt – von der ersten Beratung bis zur Lösung.</p></div>
  <div class="abs why-item" style="left:757px;top:170px"><h4>Breites Spektrum</h4><p>Durch unsere thematische Vielfalt können wir auf externe Anwälte in den meisten Fällen vollständig verzichten.</p></div>
</section>

<section class="team">
  <div class="abs eyebrow">Unser Team</div>
  <h2 class="abs serif">Die Rechtsanwälte</h2>
  <div class="abs all">ALLE ANWÄLTE ›</div>
  <div class="abs member" style="left:255px">
    <div class="ph" role="img" aria-label="Porträtfoto eines Rechtsanwalts im Anzug"></div>
    <div class="info"><h4>Tarek Halvani</h4><small>FACHANWALT · STRAFRECHT</small></div>
  </div>
  <div class="abs member" style="left:431px">
    <div class="ph" role="img" aria-label="Porträtfoto eines Rechtsanwalts im Anzug"></div>
    <div class="info"><h4>Matthias K. Berndorf</h4><small>FACHANWALT · VERKEHRSRECHT</small></div>
  </div>
  <div class="abs member" style="left:608px">
    <div class="ph" role="img" aria-label="Porträtfoto einer Rechtsanwältin" style="background:linear-gradient(180deg,#eceff1 0%,#dfe3e6 60%,#8fa3a1 100%)"></div>
    <div class="info"><h4>Sabine Lichtenau</h4><small>FACHANWÄLTIN · FAMILIENRECHT</small></div>
  </div>
  <div class="abs member" style="left:784px">
    <div class="ph" role="img" aria-label="Porträtfoto eines Rechtsanwalts im Anzug"></div>
    <div class="info"><h4>Reinhard Ostler</h4><small>RECHTSANWALT · ARBEITSRECHT</small></div>
  </div>
</section>

<section class="cta">
  <h2 class="abs serif">Rechtliche Klarheit beginnt<br>mit einem<br><span>Gespräch.</span></h2>
  <div class="abs tel"><svg width="12" height="12" viewBox="0 0 24 24" fill="#c8b791"><path d="M6.6 10.8a15.1 15.1 0 006.6 6.6l2.2-2.2a1 1 0 011-.25 11.4 11.4 0 003.6.57 1 1 0 011 1V20a1 1 0 01-1 1A17 17 0 013 4a1 1 0 011-1h3.5a1 1 0 011 1c0 1.25.2 2.45.57 3.57a1 1 0 01-.25 1z"/></svg>0831 · 472 906 20</div>
  <div class="abs hours">Montag – Freitag · 8:00 – 18:00 Uhr</div>
  <div class="abs form">ONLINE-FORMULAR <svg width="5" height="6" viewBox="0 0 5 6"><path d="M0 0l5 3-5 3z" fill="#1c1c1e"/></svg></div>

  <div class="abs foot-brand">Kanzlei am Lindenhof</div>
  <div class="abs foot-sub">RECHTSANWÄLTE &amp; FACHANWÄLTE · KEMPTEN</div>
  <div class="abs foot-addr">Lindenweg 14<br>87439 Kempten (Allgäu)</div>
  <div class="abs foot-mail">Tel. 0831 · 472 906 20<br>info@kanzlei-lindenhof.de</div>

  <div class="abs foot-col" style="left:593px;top:235px"><h5>RECHTSGEBIETE</h5><ul><li>Familienrecht</li><li>Arbeitsrecht</li><li>Verkehrsrecht</li><li>Strafrecht</li><li>Erbrecht</li><li>Mietrecht</li><li>Baurecht</li></ul></div>
  <div class="abs foot-col" style="left:744px;top:235px"><h5>KANZLEI</h5><ul><li>Über uns</li><li>Rechtsanwälte</li><li>Mitarbeiter</li><li>Karriere</li><li>Bewertungen</li><li>Downloads</li></ul></div>
  <div class="abs foot-col" style="left:896px;top:235px"><h5>KONTAKT</h5><ul><li>Terminvereinbarung</li><li>Kontaktformular</li><li>Anfahrt</li></ul></div>

  <div class="abs foot-rule"></div>
  <div class="abs legal"><span>Impressum</span><span>Datenschutz</span><span>Sitemap</span></div>
  <div class="abs copy">© 2025 Kanzlei am Lindenhof · Alle Rechte vorbehalten</div>
</section>

</body>
</html>
```